Detail Shop Business card design

i need a business card design for my new detailing company called 'Brisk's Polish Works'. i want an all black and white design . simple, direct and to the point. i want the designer to choose a fitting font to match the logothe front should have logo, address, phone and email and the back side should have a slogan and text indicating that we offer services on anything including cars, trucks, motorcycles and RVs. slogan will read "We polish what you drive"
maybe also very small on the back side the IG icon with Brisks_Polish_Works

phone 208.417.6352
address 3847 E Larkin Ave
Kellford WA 99362
email: BrisksPolish@mailvexo.com

Target Market(s)

all ages , auto enthusiasts

Industry/Entity Type

Automotive

Contact Information for Business Card

the front should have logo, address, phone and email and the back side should have a slogan and text indicating that we offer services on anything including cars, trucks, motorcycles and RVs. slogan will read "We polish what you drive"

phone 208.417.6352
address 3847 E Larkin Ave
Kellford WA 99362

Colors
000000
ffffff

Requirements
Must have
• bold font and very simple design with good spacing
Nice to have
• anything creative from the designer indicating we service any types of vehicles
Should not have
• any colors ,

```html
<!DOCTYPE html>
<html lang="en">
<head>
<meta charset="utf-8">
<title>Brisk's Polish Works – Business Card</title>
<link rel="stylesheet" href="https://fonts.googleapis.com/css2?family=Open+Sans:wght@400;600;700&display=swap">
<style>
  :root {
    --backdrop: #3b3633;
    --card: #141414;
    --ink: #ffffff;
    --ink-soft: #d9d9d9;
    --mark: #cfcfcf;
  }
  * { box-sizing: border-box; margin: 0; padding: 0; }
  html, body {
    width: 1200px; height: 864px; overflow: hidden;
    background: var(--backdrop);
    font-family: "Open Sans", Arial, sans-serif;
    color: var(--ink);
  }
  .canvas { position: relative; width: 1200px; height: 864px; }
  .card {
    position: absolute;
    width: 540px; height: 308px;
    background: var(--card);
    border-radius: 3px;
    box-shadow: 0 10px 28px rgba(0,0,0,.45);
  }
  /* back side */
  .card-back { left: 50px; top: 120px; }
  .brand-mark {
    position: absolute; left: 50%; top: 40px; transform: translateX(-50%);
    display: flex; flex-direction: column; align-items: center; gap: 10px;
  }
  .brand-dot {
    width: 60px; height: 60px; border-radius: 50%;
    border: 3px solid var(--mark);
  }
  .brand-name {
    font-weight: 700; font-size: 22px; color: var(--mark);
    white-space: nowrap; letter-spacing: .5px;
  }
  .slogan {
    position: absolute; left: 0; right: 0; top: 176px;
    text-align: center; font-weight: 700; font-size: 17px; letter-spacing: .5px;
  }
  .slogan-rule {
    position: absolute; left: 110px; right: 110px; top: 206px;
    height: 1px; background: var(--ink-soft);
  }
  .services {
    position: absolute; left: 0; right: 0; top: 216px;
    text-align: center; font-size: 12.5px; color: var(--ink-soft);
  }
  /* front side */
  .card-front { left: 610px; top: 400px; }
  .person { position: absolute; left: 34px; top: 34px; }
  .person-name { font-weight: 700; font-size: 18px; letter-spacing: .3px; }
  .person-role { font-size: 12px; letter-spacing: .5px; margin-top: 1px; }
  .contact-list {
    position: absolute; left: 34px; top: 92px; list-style: none;
    font-size: 12.5px; line-height: 19px;
  }
  .contact-list li { display: flex; align-items: center; gap: 8px; }
  .contact-list svg { width: 12px; height: 12px; fill: var(--ink); flex: none; }
  .contact-rule {
    position: absolute; left: 34px; top: 178px; width: 280px;
    height: 1px; background: var(--ink);
  }
  .front-mark {
    position: absolute; right: 30px; top: 90px;
    display: flex; flex-direction: column; align-items: center; gap: 8px;
  }
  .front-mark .brand-name { font-size: 17px; color: var(--ink); }
  .front-mark .brand-dot { width: 48px; height: 48px; border-color: var(--ink); }
  .address-rule {
    position: absolute; left: 34px; right: 30px; top: 236px;
    height: 1px; background: var(--ink);
  }
  .address {
    position: absolute; right: 30px; top: 246px; text-align: right;
    font-size: 13px; line-height: 18px;
  }
</style>
</head>
<body>
<main class="canvas">
  <section class="card card-back" aria-label="Business card back">
    <div class="brand-mark">
      <span class="brand-dot"></span>
      <span class="brand-name">Brisk's Polish Works</span>
    </div>
    <p class="slogan">WE POLISH WHAT YOU DRIVE</p>
    <div class="slogan-rule"></div>
    <p class="services">we care for every vehicle you own, from sedans and pickups to bikes &amp; campers</p>
  </section>

  <section class="card card-front" aria-label="Business card front">
    <div class="person">
      <p class="person-name">MARCUS HALE</p>
      <p class="person-role">PRESIDENT</p>
    </div>
    <ul class="contact-list">
      <li><svg viewBox="0 0 12 12" aria-hidden="true"><path d="M2 1h3l1 3-1.5 1a6 6 0 0 0 2.5 2.5L8 6l3 1v3c0 .6-.4 1-1 1A9 9 0 0 1 1 2c0-.6.4-1 1-1z"/></svg>208.417.6352</li>
      <li><svg viewBox="0 0 12 12" aria-hidden="true"><path d="M3 0h6a1 1 0 0 1 1 1v10a1 1 0 0 1-1 1H3a1 1 0 0 1-1-1V1a1 1 0 0 1 1-1zm0 2v7h6V2zm3 8a.6.6 0 1 0 0 1.2A.6.6 0 0 0 6 10z"/></svg>208 559 7140</li>
      <li><svg viewBox="0 0 12 12" aria-hidden="true"><path d="M0 2h12v8H0zm1 1v.3l5 3.4 5-3.4V3z"/></svg>BrisksPolish@mailvexo.com</li>
      <li><svg viewBox="0 0 12 12" aria-hidden="true"><path d="M6 0a6 6 0 1 0 0 12A6 6 0 0 0 6 0zm0 1.2c.8 0 1.6 1.9 1.7 4.2H4.3C4.4 3.1 5.2 1.2 6 1.2zM4.3 6.6h3.4c-.1 2.3-.9 4.2-1.7 4.2s-1.6-1.9-1.7-4.2z"/></svg>www.briskspolishworks.com</li>
    </ul>
    <div class="contact-rule"></div>
    <div class="front-mark">
      <span class="brand-dot"></span>
      <span class="brand-name">Brisk's Polish Works</span>
    </div>
    <div class="address-rule"></div>
    <p class="address">3847 E Larkin Ave<br>Kellford WA 99362</p>
  </section>
</main>
</body>
</html>
```